International Medical Company Needs a Website Design for a Support Site

We need a website design for a support site we are doing for ostomates called Bright Returns. We are an international company but this website is for our Australian market.

The website is a support site for people who are living with an Ostomy or Bowel Disease. This is a site where they can read other ostomates' stories and how they are dealing with the fact that they have to wear a pouch everyday.

The URL for our US site is: http://www.brightreturnsite.example/

We need to use the same logo but we have freedom around the color scheme. We are not fond of the brown color scheme used in our US site and are happy for designs to be submitted with alternatives.

• We want the design to be clean, inspiring, modern and inviting.
• We would like to see a design for the mainpage / homepage and one of the subpages
• We only require the PSD / image files (no HTML needed)

Attached to this project is our sitemap, an example wireframe and the logos. We are happy for you to play around with different options and don't have to stick to the layout shown in the wireframe.

If you have any further questions please ask.

Industry/Entity Type

It Company

```html
<!DOCTYPE html>
<html lang="en">
<head>
<meta charset="utf-8">
<title>Bright Returns – Sharing Stories and Giving Hope</title>
<link href="https://fonts.googleapis.com/css2?family=Source+Sans+3:ital,wght@0,400;0,600;1,400&display=swap" rel="stylesheet">
<style>
:root{
  --gold:#b0894f;
  --gold-dark:#9a7540;
  --ink:#2b2b2b;
  --text:#6f6f6f;
  --nav:#2f2f2f;
  --nav-top:#3c3c3c;
  --card-bg:#f7f7f7;
  --card-line:#dcdcdc;
  --footer:#2a2a2a;
  --white:#ffffff;
}
*{margin:0;padding:0;box-sizing:border-box}
html,body{width:1200px;height:1067px;overflow:hidden;background:var(--white)}
body{font-family:"Source Sans 3",sans-serif;color:var(--text);position:relative}
.abs{position:absolute}

/* header */
.brand{left:130px;top:88px;font-size:19px;letter-spacing:2px;color:var(--gold-dark);font-weight:600}
.country-label{left:810px;top:22px;font-size:14px;font-style:italic;color:#8a8a8a}
.country-select{left:944px;top:16px;width:125px;height:30px;background:#eeeeee;border:1px solid #e2e2e2;display:flex;align-items:center;padding-left:9px;font-size:14px;color:#666}
.flag{width:18px;height:12px;margin-right:10px;background:linear-gradient(#b4b4d8 0 0) 0 0/8px 7px no-repeat,repeating-linear-gradient(#d46 0 2px,#fff 2px 4px)}
.caret{position:absolute;right:12px;top:13px;border:4px solid transparent;border-top-color:#888}
.btn{display:flex;align-items:center;justify-content:center;gap:12px;color:var(--white);font-size:14px;text-transform:uppercase;border-radius:2px}
.btn-gold{background:linear-gradient(#bd9559,#a67f45);border:1px solid #9a743f}
.btn-dark{background:linear-gradient(#3a3a3a,#222);border:1px solid #1a1a1a}
.chev{width:6px;height:6px;border-top:2px solid currentColor;border-right:2px solid currentColor;transform:rotate(45deg)}
.header-share{left:685px;top:69px;width:153px;height:38px}
.search{left:849px;top:69px;width:221px;height:38px;border:1px solid #e2e2e2;display:flex;align-items:center;padding-left:13px;font-size:13px;font-style:italic;color:#aaa}
.search-divider{position:absolute;right:43px;top:6px;width:1px;height:25px;background:#e2e2e2}
.search svg{position:absolute;right:10px;top:9px}

/* navigation */
.main-nav{left:0;top:129px;width:1200px;height:47px;background:linear-gradient(var(--nav-top),var(--nav) 60%,#262626)}
.main-nav a{position:absolute;top:0;height:47px;line-height:47px;color:var(--white);text-decoration:none;font-size:13.5px;text-transform:uppercase}
.main-nav a.active{background:var(--gold);left:133px;width:105px;text-align:center}

/* hero */
.hero{left:130px;top:195px;width:940px;height:390px;overflow:hidden}
.hero-photo{position:absolute;inset:0;background:linear-gradient(90deg,rgba(0,0,0,0) 55%,#1a1a1a 75%,#0e0e0e),linear-gradient(165deg,#8e9db1 0%,#c3cad3 45%,#e9ebee 90%)}
.hero-title{left:108px;top:62px;color:var(--white);font-size:24px;line-height:40px;text-transform:uppercase;text-shadow:0 1px 3px rgba(0,0,0,.25)}
.hero-title b{font-size:33px;font-weight:600}
.hero-text{left:109px;top:165px;width:400px;font-size:15px;line-height:24px;color:#2d2d2d}
.hero-share{left:109px;top:271px;width:144px;height:39px}
.hero-or{left:267px;top:283px;font-size:13px;color:#444}
.hero-read{left:298px;top:271px;width:144px;height:39px}
.arrow-prev{left:12px;top:183px}
.arrow-next{left:893px;top:183px}

/* cards */
.card{top:637px;width:300px;height:291px;background:var(--card-bg);border:1px solid var(--card-line)}
.card-photo{position:absolute;left:10px;top:10px;width:278px;height:151px}
.card h2{position:absolute;left:14px;top:180px;font-size:18px;font-weight:400;color:var(--gold-dark)}
.card p{position:absolute;left:14px;top:212px;width:272px;font-size:13.5px;line-height:20px;color:#7a7a7a}
.more{font-style:italic;color:var(--gold);margin-left:8px}
.news h2{top:17px;left:17px}
.news-item{position:absolute;left:15px;width:275px}
.news-photo{position:absolute;left:0;top:0;width:60px;height:60px}
.news-date{position:absolute;left:75px;top:-2px;font-size:12.5px;color:var(--gold-dark)}
.news-item p{position:absolute;left:75px;top:22px;width:200px;font-size:13.5px;line-height:18px}
.news-more{position:absolute;left:76px;top:68px;font-size:12.5px;font-style:italic;color:var(--gold)}
.news-divider{position:absolute;left:15px;top:161px;width:272px;height:1px;background:#e3e3e3}

/* footer */
.site-footer{left:0;top:979px;width:1200px;height:88px;background:var(--footer)}
.social{position:absolute;top:34px;width:28px;height:28px;border-radius:50%;background:#8c8c8c}
.footer-links{position:absolute;right:134px;top:36px;font-size:13.5px;color:#bdbdbd}
.footer-links span{margin:0 8px;color:#888}
</style>
</head>
<body>

<header>
  <div class="abs brand">BRIGHT RETURNS</div>
  <div class="abs country-label">Choose Your Country:</div>
  <div class="abs country-select"><span class="flag"></span>Country<span class="caret"></span></div>
  <a class="abs btn btn-gold header-share">Share a Story <span class="chev"></span></a>
  <div class="abs search">Search here...
    <span class="search-divider"></span>
    <svg width="22" height="20" viewBox="0 0 22 20"><circle cx="8" cy="8" r="6" fill="none" stroke="#555" stroke-width="2.4"/><line x1="12.5" y1="12" x2="20" y2="18" stroke="#555" stroke-width="3.2" stroke-linecap="round"/></svg>
  </div>
</header>

<nav class="abs main-nav">
  <a class="active">About Us</a>
  <a style="left:282px">Personal Stories</a>
  <a style="left:433px">Tips for Living</a>
  <a style="left:576px">News</a>
  <a style="left:661px">Resources</a>
  <a style="left:772px">Contact Us</a>
</nav>

<section class="abs hero">
  <div class="hero-photo" role="img" aria-label="Silhouette of a climber helping another up a rock against a pale sky"></div>
  <h1 class="abs hero-title">Sharing <b>Stories</b> and<br>Giving <b>Hope</b></h1>
  <p class="abs hero-text">To people around the world who are facing inflammatory bowel disease, colorectal cancer, or have had ostomy surgery.</p>
  <a class="abs btn btn-dark hero-share">Share a Story <span class="chev"></span></a>
  <span class="abs hero-or">OR</span>
  <a class="abs btn btn-gold hero-read">Read Stories <span class="chev"></span></a>
  <svg class="abs arrow-prev" width="36" height="36" viewBox="0 0 36 36"><circle cx="18" cy="18" r="16" fill="none" stroke="#fff" stroke-width="2.5"/><path d="M22 9 L11 18 L22 27 L19 18 Z" fill="#fff"/></svg>
  <svg class="abs arrow-next" width="36" height="36" viewBox="0 0 36 36"><circle cx="18" cy="18" r="16" fill="none" stroke="#ccc" stroke-width="2.5"/><path d="M14 9 L25 18 L14 27 L17 18 Z" fill="#ccc"/></svg>
</section>

<main>
  <article class="abs card" style="left:130px">
    <div class="card-photo" role="img" aria-label="Smiling woman giving two thumbs up" style="background:linear-gradient(160deg,#e8e4e4,#d6cdd0 60%,#c9b7bd)"></div>
    <h2>What is Bright Returns</h2>
    <p>Excepteur sint occaecat cupidatat non proident, sunt in culpa qui officia deserunt mollit anim id est laborum <span class="more">More &gt;&gt;</span></p>
  </article>

  <article class="abs card" style="left:450px">
    <div class="card-photo" role="img" aria-label="Two women reading a book together outdoors" style="background:linear-gradient(120deg,#6f7a55,#4a4038 50%,#2c2a2a 80%,#7b6a58)"></div>
    <h2>Share a Story</h2>
    <p>Excepteur sint occaecat cupidatat non proident, sunt in culpa qui officia deserunt mollit anim id est laborum <span class="more">More &gt;&gt;</span></p>
  </article>

  <aside class="abs card news" style="left:770px">
    <h2>Recent News</h2>
    <svg class="abs" style="left:267px;top:20px" width="20" height="20" viewBox="0 0 20 20"><circle cx="10" cy="10" r="8.5" fill="none" stroke="#777" stroke-width="1.4"/><path d="M8 5.5 L13.5 10 L8 14.5 Z" fill="#777"/></svg>
    <div class="news-item" style="top:63px">
      <div class="news-photo" role="img" aria-label="Portrait of a man wearing glasses" style="background:linear-gradient(#9a8e88,#c7a892)"></div>
      <span class="news-date">10 Mar 2014</span>
      <p>Excepteur sint occaecat cupidatat non proident, sunt in culpa qui</p>
      <span class="news-more">More &gt;&gt;</span>
    </div>
    <div class="news-divider"></div>
    <div class="news-item" style="top:189px">
      <div class="news-photo" role="img" aria-label="Portrait of a smiling young man" style="background:linear-gradient(#6d5a4c,#c69a78)"></div>
      <span class="news-date">10 Mar 2014</span>
      <p>Excepteur sint occaecat cupidatat non proident, sunt in culpa qui</p>
      <span class="news-more">More &gt;&gt;</span>
    </div>
  </aside>
</main>

<footer class="abs site-footer">
  <span class="social" style="left:136px"></span>
  <span class="social" style="left:170px"></span>
  <span class="social" style="left:204px"></span>
  <span class="social" style="left:237px"></span>
  <div class="footer-links">Legal Notice<span>/</span>Privacy Policy<span>/</span>Sitemap</div>
</footer>

</body>
</html>
```